Road Construction Company needs business cards

We would like a new business card designed for our business.

We're a road construction company based in Qld, Australia.

Can the business card please have the following information on it.

Name: Warren Halbeck
Position: General Manager
Phone: 0472 915 348
Email: Warren.halbeck@tovrin.com.au
Address: 87 Marrow Ave, Pendlebay, QLD, 4023
Website: www.tovrin.com.au

Visually we'd like the card to be professional and simple.

Attached is our logo.

Our website is www.tovrin.com.au

Target Market(s)

Men aged 25-60

Contact Information for Business Card

As listed in project description

Font styles to use
Serif

Requirements
Must have
• Large logo on back of card

```html
<!DOCTYPE html>
<html lang="en">
<head>
<meta charset="utf-8">
<title>Tovrin Business Card</title>
<link href="https://fonts.googleapis.com/css2?family=Open+Sans:wght@400;600;700;800&display=swap" rel="stylesheet">
<style>
  :root {
    --backdrop: #2a2d33;
    --card-white: #ffffff;
    --brand-blue: #1152a8;
    --band-blue: #2b87cf;
    --back-blue: #1257a8;
    --ink: #111111;
    --rule: #333333;
  }
  * { margin: 0; padding: 0; box-sizing: border-box; }
  html, body { width: 1200px; height: 780px; overflow: hidden; }
  body {
    background: var(--backdrop);
    font-family: "Open Sans", Arial, sans-serif;
    display: flex;
    align-items: center;
    justify-content: center;
    gap: 50px;
  }
  .card {
    position: relative;
    width: 540px;
    height: 310px;
    border-radius: 18px;
    overflow: hidden;
    box-shadow: 0 14px 30px rgba(0,0,0,0.45);
  }
  .card--front { background: var(--card-white); }
  .card--back {
    background: var(--back-blue);
    display: flex;
    align-items: center;
    justify-content: center;
  }
  .wordmark {
    font-weight: 800;
    letter-spacing: 1px;
    line-height: 1;
  }
  .card--front .wordmark {
    position: absolute;
    left: 38px;
    top: 92px;
    font-size: 50px;
    color: var(--brand-blue);
  }
  .card--back .wordmark {
    font-size: 96px;
    color: var(--ink);
    letter-spacing: 3px;
  }
  .divider {
    position: absolute;
    left: 240px;
    top: 60px;
  }
  .person {
    position: absolute;
    left: 296px;
    top: 74px;
  }
  .person__name {
    font-size: 27px;
    font-weight: 700;
    color: var(--brand-blue);
    line-height: 1.1;
  }
  .person__role {
    font-size: 14px;
    color: var(--ink);
    margin-bottom: 12px;
  }
  .contact-list { list-style: none; }
  .contact-list li {
    display: flex;
    align-items: center;
    gap: 8px;
    font-size: 13.5px;
    color: var(--ink);
    line-height: 1.55;
  }
  .contact-list svg { flex: none; }
  .address-band {
    position: absolute;
    left: 0;
    bottom: 0;
    width: 100%;
    height: 46px;
    background: var(--band-blue);
    color: var(--card-white);
    font-size: 15px;
    display: flex;
    align-items: center;
    padding-left: 38px;
  }
</style>
</head>
<body>

  <section class="card card--front" aria-label="Business card front">
    <div class="wordmark">TOVRIN</div>

    <svg class="divider" width="40" height="170" viewBox="0 0 40 170" aria-hidden="true">
      <line x1="38" y1="0" x2="2" y2="170" stroke="var(--rule)" stroke-width="1"/>
    </svg>

    <div class="person">
      <div class="person__name">Warren Halbeck</div>
      <div class="person__role">General Manager</div>
      <ul class="contact-list">
        <li>
          <svg width="12" height="12" viewBox="0 0 12 12" aria-hidden="true">
            <path d="M3 1 L5 3.5 L4 5 Q5 7 7 8 L8.5 7 L11 9 L10 11 Q5 11 1 5 Q1 2 3 1 Z" fill="var(--band-blue)"/>
          </svg>
          0472 915 348
        </li>
        <li>
          <svg width="12" height="12" viewBox="0 0 12 12" aria-hidden="true">
            <circle cx="6" cy="6" r="5" fill="none" stroke="var(--band-blue)" stroke-width="1.3"/>
            <line x1="1" y1="6" x2="11" y2="6" stroke="var(--band-blue)" stroke-width="1"/>
            <ellipse cx="6" cy="6" rx="2.2" ry="5" fill="none" stroke="var(--band-blue)" stroke-width="1"/>
          </svg>
          www.tovrin.com.au
        </li>
        <li>
          <svg width="12" height="12" viewBox="0 0 12 12" aria-hidden="true">
            <rect x="1" y="2.5" width="10" height="7" fill="none" stroke="var(--band-blue)" stroke-width="1.3"/>
            <path d="M1 2.5 L6 6.5 L11 2.5" fill="none" stroke="var(--band-blue)" stroke-width="1.1"/>
          </svg>
          Warren.halbeck@tovrin.com.au
        </li>
      </ul>
    </div>

    <div class="address-band">87 Marrow Ave, Pendlebay, QLD, 4023</div>
  </section>

  <section class="card card--back" aria-label="Business card back">
    <div class="wordmark">TOVRIN</div>
  </section>

</body>
</html>
```